Hong Kong based International Remittance and ForEx company requires website design

We need a website designed for a new European - Hong Kong based ForEx & fund remittence entity.

The company specialises in larger corporate & high net worth private client trades, therefore the design must aesthetically reflect this (sophisticated). As a theme colour, financial entities tend to use either blue or red; if blue, our preference is a darker blue. Visually, our preference is less copy, more imagery.

Number of pages would be limited; landing (home), about us, client registration (x1 Corporate form, x1 Private Client form), Contact Us.

Have uploaded the existing logo - please note this is to be redesigned, although the colour scheme will remain the same. Please also note that copy will follow - please use Lorem Ipsum.

Target Market(s)

Medium to large Corporations. High net worth individuals.

Industry/Entity Type

Financial Service

Coding

Coded - Design and coding required

Number of Pages Required

4 page

Font styles to use
Serif

Requirements
Nice to have
• ForEx ticker,

```html
<!DOCTYPE html>
<html lang="en">
<head>
<meta charset="utf-8">
<title>Harbourline Incorporation Limited</title>
<link rel="stylesheet" href="https://fonts.googleapis.com/css2?family=Gentium+Book+Plus:wght@400;700&display=swap">
<style>
:root{
  --ink:#2b2f36;
  --muted:#6b7079;
  --accent:#7f9fc8;
  --accent-soft:#b8cde6;
  --hero-top:#c9d3e3;
  --hero-bottom:#3b4453;
  --caption:#14171d;
  --ticker-label:#bdbdbd;
  --down:#c8202a;
  --index:#2f6aa5;
  --about:#7f8da3;
  --white:#ffffff;
  --rule:#dfe3ea;
}
*{box-sizing:border-box;margin:0;padding:0}
html,body{width:1200px;height:2350px;overflow:hidden}
body{font-family:"Gentium Book Plus",Georgia,serif;color:var(--ink);background:var(--white);position:relative}
.site-header{position:absolute;top:0;left:0;width:1200px;height:131px;background:var(--white)}
.brand{position:absolute;left:144px;top:44px;display:flex;align-items:center;gap:12px;font-size:42px;color:var(--ink)}
.brand-dot{width:22px;height:22px;border-radius:50%;background:var(--accent)}
.language{position:absolute;right:144px;top:22px;display:flex;align-items:center;gap:8px;font-size:10px;color:#9aa0a8;letter-spacing:.5px}
.language-select{border:1px solid #ccd;border-radius:3px;padding:6px 10px;font-size:11px;color:var(--ink);display:flex;gap:8px;align-items:center}
.main-nav{position:absolute;right:144px;top:70px;display:flex;gap:28px;font-size:13.5px;letter-spacing:.3px}
.main-nav a{color:var(--ink);text-decoration:none;padding-bottom:10px}
.main-nav a.active{color:var(--accent);border-bottom:3px solid var(--accent-soft)}
.hero{position:absolute;top:131px;left:0;width:1200px;height:669px;background:linear-gradient(180deg,var(--hero-top) 0%,#8e9bb2 35%,var(--hero-bottom) 100%)}
.hero-caption{position:absolute;left:0;bottom:0;width:100%;height:105px;background:rgba(20,23,29,.85);display:flex;align-items:center;justify-content:center;color:var(--white);font-size:27px}
.hero-arrow{position:absolute;top:38px;width:30px;height:30px}
.hero-arrow.prev{left:78px}.hero-arrow.next{right:78px}
.ticker{position:absolute;top:800px;left:0;width:1200px;height:64px;background:var(--white);display:flex;align-items:center}
.ticker-label{width:240px;height:64px;background:var(--ticker-label);color:var(--white);display:flex;align-items:center;justify-content:center;font-size:18px;letter-spacing:1px}
.ticker-item{font-size:15px;margin-left:64px;display:flex;gap:10px;color:var(--ink)}
.ticker-item:first-of-type{margin-left:64px}
.ticker-item .name{color:var(--index)}
.ticker-item .change{color:var(--down)}
.welcome{position:absolute;top:864px;left:0;width:1200px;height:329px;background:var(--accent-soft)}
.welcome-photo{position:absolute;left:144px;top:54px;width:363px;height:223px;border:5px solid #eef1f5;background:linear-gradient(135deg,#c6d3e6 0%,#4f6891 45%,#14213d 100%);box-shadow:0 2px 6px rgba(0,0,0,.25)}
.welcome-title{position:absolute;left:534px;top:48px;width:522px;font-size:26px;font-weight:400;color:var(--white);letter-spacing:.5px;padding-bottom:14px;border-bottom:1px solid rgba(255,255,255,.7)}
.welcome-text{position:absolute;left:534px;top:122px;width:522px;font-size:12.5px;line-height:29px;color:var(--white)}
.expertise{position:absolute;top:1193px;left:0;width:1200px;height:558px}
.section-title{position:absolute;left:144px;top:52px;width:912px;text-align:center;font-size:26px;font-weight:400;color:var(--accent);padding-bottom:12px;border-bottom:1px solid var(--rule)}
.service{position:absolute;top:132px;width:285px}
.service-photo{width:285px;height:185px;border:4px solid #e9ecf1;box-shadow:0 1px 4px rgba(0,0,0,.2)}
.service-title{margin-top:32px;font-size:18.5px;font-weight:400;color:var(--ink)}
.service-text{margin-top:20px;font-size:10.5px;line-height:19px;color:var(--muted)}
.photo-tablet{background:linear-gradient(135deg,#7a8a6c 0%,#c8c8c0 45%,#3f5a7a 100%)}
.photo-handshake{background:linear-gradient(135deg,#f1ede6 0%,#b7c4d6 50%,#34507c 100%)}
.photo-desk{background:linear-gradient(135deg,#c9b6a3 0%,#eef1f6 50%,#8fa8c8 100%)}
.about{position:absolute;top:1751px;left:0;width:1200px;height:400px;background:linear-gradient(180deg,#8895ab 0%,var(--about) 60%,#9aa6b8 100%)}
.about-title{position:absolute;top:102px;width:100%;text-align:center;font-size:25px;font-weight:400;color:var(--white)}
.about-text{position:absolute;top:157px;left:144px;width:912px;text-align:center;font-size:13.5px;line-height:24px;color:var(--white)}
.about-button{position:absolute;left:527px;top:289px;width:136px;height:45px;border:1px solid var(--white);color:var(--white);font-size:12.5px;display:flex;align-items:center;justify-content:center;letter-spacing:.5px}
.site-footer{position:absolute;top:2151px;left:0;width:1200px;height:199px;text-align:center}
.footer-nav{margin-top:40px;font-size:18px;color:var(--ink)}
.footer-nav span.sep{margin:0 8px}
.footer-legal{margin-top:28px;font-size:12.5px;color:var(--ink)}
.footer-legal span.sep{margin:0 5px}
.copyright{margin-top:14px;font-size:12px;color:var(--ink)}
</style>
</head>
<body>
<header class="site-header">
  <div class="brand"><span class="brand-dot"></span>Harbourline</div>
  <div class="language">LANGUAGE :
    <span class="language-select">ENG
      <svg width="9" height="6" viewBox="0 0 9 6"><path d="M1 1l3.5 3.5L8 1" stroke="#333" stroke-width="1.6" fill="none"/></svg>
    </span>
  </div>
  <nav class="main-nav">
    <a class="active">ABOUT US</a><a>INTERNATIONAL</a><a>PAYMENTS</a><a>CONTACT US</a><a>CLIENT</a><a>APPLICATION</a>
  </nav>
</header>

<section class="hero" role="img" aria-label="Night skyline of Hong Kong skyscrapers over the harbour">
  <div class="hero-caption">
    <svg class="hero-arrow prev" viewBox="0 0 30 30"><path d="M19 6l-9 9 9 9" stroke="#fff" stroke-width="3.5" fill="none"/></svg>
    We are a new ForEx &amp; fund remittance entity based in European - Hong Kong
    <svg class="hero-arrow next" viewBox="0 0 30 30"><path d="M11 6l9 9-9 9" stroke="#fff" stroke-width="3.5" fill="none"/></svg>
  </div>
</section>

<section class="ticker">
  <div class="ticker-label">FOREX&nbsp; TICKER</div>
  <div class="ticker-item"><span class="name">TECHX</span><span>$ 16,78</span><span class="change">0,31 ▼ 1,81%</span></div>
  <div class="ticker-item"><span class="name">TREAS.</span><span>$ 16,78</span><span class="change">0,31 ▼ 1,81%</span></div>
  <div class="ticker-item"><span class="name">INDEX 500</span><span>$ 16,78</span><span class="change">0,31 ▼ 1,81%</span></div>
</section>

<section class="welcome">
  <div class="welcome-photo" role="img" aria-label="Glass tower reflecting clouds with a digital stock price board"></div>
  <h2 class="welcome-title">WELCOME TO HARBOURLINE</h2>
  <p class="welcome-text">Harbourline Incorporation Limited is a regulated Money Service Operator Number (16-04-02218), licensed authorised by the Hong Kong Customs and Excise.We provide the international settlement and reconciliation of funds for and on behalf of our clients which include both corporates and individuals.As well as acting as a remittance entity we also provide foreign exchange services and work closely with our clients to source</p>
</section>

<section class="expertise">
  <h2 class="section-title">OUR EXPERTISE</h2>
  <article class="service" style="left:144px">
    <div class="service-photo photo-tablet" role="img" aria-label="Hands holding a tablet showing a financial chart"></div>
    <h3 class="service-title">International Money Transfer</h3>
    <p class="service-text">Lorem Ipsum is simply dummy text of the printing and typesetting industry. Lorem Ipsum has been the industry's standard dummy text ever since the 1500s, when an unknown printer took a galley of type and scrambled it to make a type specimen book.</p>
  </article>
  <article class="service" style="left:456px">
    <div class="service-photo photo-handshake" role="img" aria-label="Business people meeting over a city backdrop"></div>
    <h3 class="service-title">Foreign Exchange</h3>
    <p class="service-text">Lorem Ipsum is simply dummy text of the printing and typesetting industry. Lorem Ipsum has been the industry's standard dummy text ever since the 1500s, when an unknown printer took a galley of type and scrambled it to make a type specimen book.</p>
  </article>
  <article class="service" style="left:765px">
    <div class="service-photo photo-desk" role="img" aria-label="Laptop and printed charts on an office desk"></div>
    <h3 class="service-title">Paying &amp; Receiving Agency</h3>
    <p class="service-text">Lorem Ipsum is simply dummy text of the printing and typesetting industry. Lorem Ipsum has been the industry's standard dummy text ever since the 1500s, when an unknown printer took a galley of type and scrambled it to make a type specimen book.</p>
  </article>
</section>

<section class="about" role="img" aria-label="Faded Hong Kong skyline behind the about us text">
  <h2 class="about-title">ABOUT US</h2>
  <p class="about-text">Harbourline is a leading provider of international payment services and foreign exchange to corporations and individuals covering most of the world including;&nbsp; throughout Asia, South America, and Europe.We engage with our clients with unmatched personalised service and aim to establish longevity with all our client relationships. Coupled with our excellent customer service, highly competitive rates and in depth market knowledge we provide a simple, reliable and cost effective service to all of our clients.</p>
  <div class="about-button">CONTACT US</div>
</section>

<footer class="site-footer">
  <div class="footer-nav">About Us<span class="sep">|</span>International<span class="sep">|</span>Payments<span class="sep">|</span>Contact Us<span class="sep">|</span>Client<span class="sep">|</span>Application</div>
  <div class="footer-legal">Terms &amp; Conditions<span class="sep">|</span>Peace of Mind<span class="sep">|</span>Data Protection &amp; Privacy<span class="sep">|</span>Anti Money Laundering<span class="sep">|</span>Legal</div>
  <div class="copyright">© 2016 | All Rights Reserved</div>
</footer>
</body>
</html>
```